Redesign and move to Wordpress for corvandel.com

Our website needs a redesign and at the same time we are moving it to Wordpress. Please help us with a new digital professional look and feel.

We are an Australian Software Engineering company specialising in advanced software development using in A.I., PLatform Engineering, Integration and Cloud. See the current corvandel.com for more information about us.

```html
<!DOCTYPE html>
<html lang="en">
<head>
<meta charset="utf-8">
<title>Corvandel – Custom Integration Solutions</title>
<link rel="stylesheet" href="https://fonts.googleapis.com/css2?family=Catamaran:wght@400;500;600;700&family=Lato:wght@400;700&display=swap">
<style>
:root{
  --blue:#1b4f98;
  --blue-dark:#1d4a8c;
  --teal:#45b5a9;
  --ink:#1f1f1f;
  --text:#3a3a3a;
  --red:#d7322b;
  --footer:#1e1e1e;
  --white:#fff;
  --line:#d9d9d9;
}
*{box-sizing:border-box;margin:0;padding:0}
html,body{width:1200px;height:4464px;overflow:hidden}
body{position:relative;background:var(--white);font-family:"Lato",sans-serif;color:var(--text)}
section,header,footer{position:absolute;left:0;width:1200px}
.abs{position:absolute}
.heading{font-family:"Catamaran",sans-serif;font-weight:600;color:var(--ink)}
.btn{position:absolute;display:flex;align-items:center;justify-content:center;font-family:"Lato",sans-serif;font-weight:700;font-size:15px;color:var(--white);border-radius:2px}
.btn-blue{background:var(--blue-dark)}
.btn-teal{background:var(--teal)}
.photo{position:absolute;border-radius:10px}

/* header */
.site-header{top:0;height:107px}
.brand-mark{left:111px;top:31px;width:44px;height:44px;background:var(--blue-dark)}
.brand-name{left:168px;top:26px;font-family:"Catamaran",sans-serif;font-weight:500;font-size:36px;color:var(--blue-dark);letter-spacing:1px}
.nav{top:38px;height:30px;display:flex;align-items:center;font-size:15px;color:#444}
.nav-home{left:442px;width:59px;background:var(--teal);color:#fff;justify-content:center;border-radius:2px}
.cta{left:884px;top:33px;width:203px;height:42px;font-size:15px}

/* hero */
.hero{top:107px;height:600px}
.hero-panel{left:0;top:0;width:600px;height:600px;background:linear-gradient(135deg,#1c55a3,#17468a)}
.hero-photo{left:600px;top:0;width:600px;height:600px;border-radius:0;background:linear-gradient(135deg,#d9dde2,#8b939c 55%,#4b4f57)}
.hero-title{left:111px;top:122px;width:470px;font-size:51px;line-height:60px;color:#fff}
.hero-text{left:111px;top:325px;width:400px;font-size:15px;line-height:26px;color:#fff}
.hero-btn{left:111px;top:431px;width:127px;height:43px}

/* about */
.about{top:707px;height:687px}
.about-title{left:655px;top:78px;font-size:40px}
.about-title span,.accent{color:var(--teal)}
.about-text{left:655px;width:440px;font-size:14.6px;line-height:22.5px}
.about-btn{left:655px;top:555px;width:127px;height:44px}

/* services */
.services{top:1394px;height:817px}
.services-panel{left:111px;top:0;width:1089px;height:370px;background:var(--teal);border-radius:22px 0 0 22px}
.services-title{left:168px;top:58px;font-size:39px;color:#fff}
.services-intro{left:168px;top:126px;width:715px;font-size:17px;line-height:24px;color:#fff}
.round-arrow{position:absolute;width:30px;height:30px}
.service-card{position:absolute;top:231px;width:248px}
.service-card .photo{position:relative;display:block;width:248px;height:237px;border-radius:0}
.service-card h3{margin-top:18px;font-family:"Catamaran",sans-serif;font-weight:600;font-size:21px;line-height:26px;color:var(--ink);height:52px}
.service-card p{margin-top:16px;font-size:13.8px;line-height:22px;height:132px}
.service-card .btn{position:relative;width:127px;height:43px}

/* partners */
.partners{top:2211px;height:130px}
.partner{position:absolute;top:36px;display:flex;align-items:center;gap:10px;font-family:"Catamaran",sans-serif;font-weight:700;font-size:44px;color:#222;line-height:1}
.partner i{display:block;background:#222}

/* newsletter */
.newsletter{top:2421px;left:40px;width:1118px;height:381px;background:linear-gradient(135deg,#1c55a3,#17468a);border-radius:6px}
.news-head{left:0;width:1118px;text-align:center;font-size:39px;line-height:46px;color:#fff}
.field{position:absolute;background:#fff;border:1px solid #cfcfcf;font-size:14px;color:#333;display:flex;align-items:center;padding-left:20px}
.register{left:0;width:1118px;top:286px;text-align:center;font-size:17px;color:#fff}

/* news */
.news{top:2860px;height:540px}
.news-title{left:0;width:1200px;top:14px;text-align:center;font-size:42px}
.article{position:absolute;top:88px;width:300px}
.article .photo{position:relative;display:block;width:291px;height:218px}
.article h4{margin-top:16px;font-family:"Catamaran",sans-serif;font-weight:600;font-size:23px;color:var(--teal);line-height:28px}
.article p{margin-top:8px;font-size:13.8px;line-height:21.5px;color:#333}
.article a{color:var(--blue-dark);text-decoration:underline}
.article .more{display:block;margin-top:12px;color:var(--blue-dark);font-weight:700;text-decoration:none}

/* calendar + booking */
.booking{top:3400px;height:645px}
.calendar{left:111px;top:25px;width:499px;height:534px;background:#fff;box-shadow:0 2px 10px rgba(0,0,0,.18)}
.cal-head{left:0;top:0;width:499px;height:130px;background:var(--blue-dark);color:#fff;font-family:"Catamaran",sans-serif}
.cal-month{left:28px;top:38px;font-size:52px;font-weight:600;letter-spacing:1px}
.cal-year{right:20px;top:10px;font-size:80px;font-weight:600}
.cal-row{position:absolute;left:44px;width:420px;display:grid;grid-template-columns:repeat(7,57px);align-items:center;justify-items:center;font-family:"Catamaran",sans-serif;font-size:31px;font-weight:500;color:var(--ink)}
.cal-row.days{font-size:20px;color:#555;top:168px;height:34px}
.cal-row.week{height:47px;border-bottom:1px solid var(--line)}
.sun{color:var(--red)}
.today{background:var(--teal);color:#fff;width:46px;height:40px;display:flex;align-items:center;justify-content:center}
.wk{position:absolute;left:25px;font-size:12px;color:#888}
.book-title{left:688px;top:14px;width:440px;font-size:41px;line-height:47px}
.avatar{left:808px;top:169px;width:86px;height:86px;border-radius:50%;background:linear-gradient(135deg,#6b5a4e,#2c2623)}
.blue-label{font-weight:700;color:var(--blue-dark);font-size:16px}
.slot{position:absolute;width:69px;height:35px;background:var(--blue-dark);color:#fff;font-size:13px;display:flex;align-items:center;justify-content:center}

/* footer */
.site-footer{top:4045px;height:419px;background:var(--footer);color:#fff}
.foot-title{font-family:"Catamaran",sans-serif;font-weight:600;font-size:21px;color:#fff}
.foot-link{position:absolute;left:113px;font-size:14px}
.foot-text{font-size:14px;line-height:26px}
.social{position:absolute;top:278px;width:26px;height:26px;border-radius:3px;background:#fff}
.copyright{left:0;width:1200px;top:395px;text-align:center;font-size:12px}
</style>
</head>
<body>

<header class="site-header">
  <div class="abs brand-mark" aria-hidden="true"></div>
  <div class="abs brand-name">corvandel</div>
  <div class="abs nav nav-home">Home</div>
  <div class="abs nav" style="left:532px">About</div>
  <div class="abs nav" style="left:612px">Services</div>
  <div class="abs nav" style="left:707px">Blog</div>
  <div class="abs nav" style="left:777px">Contact</div>
  <svg class="abs" style="left:850px;top:44px" width="18" height="18" viewBox="0 0 18 18" fill="none" stroke="#333" stroke-width="2"><circle cx="7.5" cy="7.5" r="5.5"/><path d="M11.5 11.5l5 5"/></svg>
  <div class="btn btn-teal cta">Schedule a Consultation</div>
</header>

<section class="hero">
  <div class="abs hero-panel"></div>
  <div class="photo hero-photo" role="img" aria-label="Three colleagues in an office looking at a laptop screen together"></div>
  <h1 class="abs heading hero-title">Custom Integration Solutions Tailored For Your Success</h1>
  <p class="abs hero-text">Delivering scalable, cutting-edge solutions with Vestrelle Gold Partner expertise. Let's simplify your integration journey together.</p>
  <div class="btn btn-teal hero-btn">Get Started</div>
</section>

<section class="about">
  <div class="photo" style="left:113px;top:113px;width:220px;height:455px;background:linear-gradient(160deg,#6f8fb4,#243d66)" role="img" aria-label="Woman working on a tablet in a dark server room"></div>
  <div class="photo" style="left:354px;top:87px;width:203px;height:241px;background:radial-gradient(circle at 50% 45%,#4f8df0,#0d2a7a 70%)" role="img" aria-label="Glowing blue microchip layers"></div>
  <div class="photo" style="left:357px;top:351px;width:217px;height:248px;background:linear-gradient(160deg,#39506f,#0f1d33)" role="img" aria-label="Hand touching a digital checklist interface"></div>
  <h2 class="abs heading about-title">About <span>Us</span></h2>
  <p class="abs about-text" style="top:155px">At Corvandel, we craft bespoke software solutions that are not available on the market. By building organizations market-leading products, process automation, legacy system enablement, or advanced intelligent systems, we empower our customers to achieve a competitive edge in their industry.</p>
  <p class="abs about-text" style="top:295px">Since our inception in 2013, we have been on a mission to make complex custom enterprise integration accessible to any organization, regardless of industry, size, or location. Our journey began with a focus on Integration Architecture, quickly moving into delivering bespoke systems integration using Vestrelle technologies like Talvex Bus, Quirnet, Vestrelle SQL Engine, and Omberlink. Our commitment to excellence quickly earned us recognition, and in 2014, we became a proud Vestrelle Gold Partner, achieving this accolade with the creation of our first 100% native Skyvessa cloud solution.</p>
  <div class="btn btn-blue about-btn">Read More</div>
</section>

<section class="services">
  <div class="abs services-panel"></div>
  <h2 class="abs heading services-title">Our Services</h2>
  <p class="abs services-intro">Innovating enterprise integration with bespoke solutions, cloud-native technologies, and a commitment to excellence. Transform your business with seamless connectivity and modern agility</p>
  <svg class="round-arrow" style="left:1005px;top:129px" viewBox="0 0 30 30"><circle cx="15" cy="15" r="15" fill="#fff"/><path d="M17.5 9l-6 6 6 6" fill="none" stroke="#333" stroke-width="2.2"/></svg>
  <svg class="round-arrow" style="left:1057px;top:129px" viewBox="0 0 30 30"><circle cx="15" cy="15" r="15" fill="#fff"/><path d="M12.5 9l6 6-6 6" fill="none" stroke="#333" stroke-width="2.2"/></svg>

  <article class="service-card" style="left:165px">
    <div class="photo" style="background:linear-gradient(160deg,#8fb4d9,#2a4a73 60%,#15243a)" role="img" aria-label="Engineer at a desk with multiple monitors"></div>
    <h3>Enterprise Systems Integration</h3>
    <p>Enterprise systems integration is the process of connecting various IT systems, applications, and data sources within an organization to work seamlessly together.</p>
    <div class="btn btn-blue">Read More</div>
  </article>
  <article class="service-card" style="left:432px">
    <div class="photo" style="background:radial-gradient(circle at 60% 40%,#5fc7ef,#0f4c8c 55%,#0a2a55)" role="img" aria-label="Hand holding a glowing cloud network icon"></div>
    <h3>Microservices</h3>
    <p>Microservices is an architectural style that structures an application as a collection of small, autonomous services modeled around a business domain.</p>
    <div class="btn btn-blue">Read More</div>
  </article>
  <article class="service-card" style="left:700px">
    <div class="photo" style="background:linear-gradient(160deg,#6fa3d8,#2d5e9a 55%,#1a2f52)" role="img" aria-label="Hands typing on a laptop with floating app icons"></div>
    <h3>Platform Engineering</h3>
    <p>Platform engineering involves creating and managing the tools and processes that allow software teams to work more efficiently and independently.</p>
    <div class="btn btn-blue">Read More</div>
  </article>
  <article class="service-card" style="left:968px">
    <div class="photo" style="background:radial-gradient(circle at 45% 45%,#c9853f,#5a2a1e 55%,#1d2a3a)" role="img" aria-label="Glowing AI chip inside a head outline"></div>
    <h3>Conversational AI</h3>
    <p>Conversational AI technology is a specialized branch of artificial intelligence that allows computers to engage in human-like conversations</p>
    <div class="btn btn-blue">Read More</div>
  </article>
</section>

<section class="partners">
  <div class="partner" style="left:116px">Dravimo</div>
  <div class="partner" style="left:390px"><i style="width:30px;height:30px"></i>Vestrelle</div>
  <div class="partner" style="left:655px">Quorlane</div>
  <div class="partner" style="left:930px;font-size:36px;top:44px"><i style="width:18px;height:18px;border-radius:50%"></i>Brelvoria</div>
</section>

<section class="newsletter">
  <h2 class="abs heading news-head" style="top:74px">Australia's Largest health charity implements</h2>
  <h2 class="abs heading news-head" style="top:130px;color:var(--teal)">Corvandel API Msg Bus</h2>
  <div class="field" style="left:230px;top:206px;width:507px;height:52px">Email</div>
  <div class="btn btn-teal" style="left:751px;top:206px;width:138px;height:52px">Subscribe</div>
  <p class="abs register">Register to our newsletter to find out more.</p>
</section>

<section class="news">
  <h2 class="abs heading news-title">News &amp; <span class="accent">Articles</span></h2>
  <svg class="round-arrow" style="left:64px;top:188px;width:30px;height:30px" viewBox="0 0 30 30"><circle cx="15" cy="15" r="15" fill="#1d4a8c"/><path d="M17.5 9l-6 6 6 6" fill="none" stroke="#fff" stroke-width="2.4"/></svg>
  <svg class="round-arrow" style="left:1107px;top:188px;width:30px;height:30px" viewBox="0 0 30 30"><circle cx="15" cy="15" r="15" fill="#1d4a8c"/><path d="M12.5 9l6 6-6 6" fill="none" stroke="#fff" stroke-width="2.4"/></svg>

  <article class="article" style="left:111px">
    <div class="photo" style="background:linear-gradient(150deg,#c9c4bd,#8a7f74 60%,#4e4741)" role="img" aria-label="Two colleagues celebrating at a laptop"></div>
    <h4>Business Insights</h4>
    <p><a>How Storytelling Helps Data-driven Teams</a> Succeed (Wexmoor School of Management)<br>Winning leaders know that data alone isn't enough.</p>
    <a class="more">Read More ...</a>
  </article>
  <article class="article" style="left:453px">
    <div class="photo" style="background:linear-gradient(160deg,#a9c8f0,#2f6bc4 55%,#123a7a)" role="img" aria-label="Blue laboratory test tubes with a pipette"></div>
    <h4>Industry Research</h4>
    <p><a>QUORTA: A general-purpose framework for prompt optimization</a> (Vestrelle Research)<br>Large language models (LLMs) have revolutionized various tasks ..</p>
    <a class="more">Read More ...</a>
  </article>
  <article class="article" style="left:794px">
    <div class="photo" style="background:radial-gradient(circle at 50% 45%,#5c8ef5,#3b2a9a 50%,#0b1030)" role="img" aria-label="Glowing AI processor chip on a circuit board"></div>
    <h4>Artificial intelligence</h4>
    <p><a>Advancing transparency: Updates on responsible AI research</a> (Vestrelle Research)<br>A surge of generative AI models in the past year has fueled much discussion ..</p>
    <a class="more">Read More ...</a>
  </article>
</section>

<section class="booking">
  <div class="abs calendar">
    <div class="abs cal-head">
      <div class="abs cal-month">JANUARY</div>
      <div class="abs cal-year">2025</div>
    </div>
    <div class="cal-row days"><span class="sun">SUN</span><span>MON</span><span>TUE</span><span>WED</span><span>THU</span><span>FRI</span><span>SAT</span></div>
    <span class="wk" style="top:226px">01</span>
    <div class="cal-row week" style="top:218px"><span></span><span></span><span></span><span>1</span><span>2</span><span>3</span><span>4</span></div>
    <span class="wk" style="top:273px">02</span>
    <div class="cal-row week" style="top:265px"><span class="sun">5</span><span>6</span><span>7</span><span>8</span><span>9</span><span>10</span><span>11</span></div>
    <span class="wk" style="top:320px">03</span>
    <div class="cal-row week" style="top:312px"><span class="sun">12</span><span>13</span><span>14</span><span class="today">15</span><span>16</span><span>17</span><span>18</span></div>
    <span class="wk" style="top:367px">04</span>
    <div class="cal-row week" style="top:359px"><span class="sun">19</span><span>20</span><span>21</span><span>22</span><span>23</span><span>24</span><span>25</span></div>
    <span class="wk" style="top:414px">05</span>
    <div class="cal-row week" style="top:406px"><span class="sun">26</span><span>27</span><span>28</span><span>29</span><span>30</span><span>31</span><span></span></div>
    <svg class="round-arrow" style="left:209px;top:468px" viewBox="0 0 30 30"><circle cx="15" cy="15" r="15" fill="#1d4a8c"/><path d="M17.5 9l-6 6 6 6" fill="none" stroke="#fff" stroke-width="2.4"/></svg>
    <svg class="round-arrow" style="left:261px;top:468px" viewBox="0 0 30 30"><circle cx="15" cy="15" r="15" fill="#1d4a8c"/><path d="M12.5 9l6 6-6 6" fill="none" stroke="#fff" stroke-width="2.4"/></svg>
  </div>

  <h2 class="abs heading book-title">Book an obligation free consultation <span class="accent">with our Lead Technologist</span></h2>
  <div class="abs avatar" role="img" aria-label="Portrait of the chief technology officer"></div>
  <div class="abs blue-label" style="left:688px;top:262px;width:400px;text-align:center;padding-right:95px">Meet with our CTO</div>
  <div class="abs" style="left:688px;top:305px;font-size:16px;font-weight:700;color:#222">Meeting duration</div>
  <div class="abs" style="left:841px;top:300px;width:246px;height:31px;background:var(--teal);color:#fff;font-size:13px;display:flex;align-items:center;justify-content:center">30 Mins</div>
  <div class="abs blue-label" style="left:688px;top:350px">What time works best?</div>
  <div class="abs" style="left:688px;top:377px;font-size:16px;color:#333">Showing times for 15 January 2025</div>
  <div class="abs" style="left:688px;top:417px;width:399px;height:31px;background:var(--teal);color:#fff;font-size:12px;display:flex;align-items:center;padding-left:20px">UTC +05:30 New Delhi, Mumbai, Calcutta
    <svg class="abs" style="right:12px;top:12px" width="10" height="7" viewBox="0 0 10 7"><path d="M1 1l4 4 4-4" fill="none" stroke="#fff" stroke-width="1.4"/></svg>
  </div>
  <div class="slot" style="left:688px;top:472px">03:30</div>
  <div class="slot" style="left:770px;top:472px">03:45</div>
  <div class="slot" style="left:853px;top:472px">04:00</div>
  <div class="slot" style="left:935px;top:472px">04:15</div>
  <div class="slot" style="left:1018px;top:472px">04:30</div>
  <div class="slot" style="left:688px;top:524px">04:45</div>
  <div class="slot" style="left:770px;top:524px">05:00</div>
  <div class="slot" style="left:853px;top:524px">05:15</div>
  <div class="slot" style="left:935px;top:524px">05:30</div>
  <div class="slot" style="left:1018px;top:524px">05:45</div>
</section>

<footer class="site-footer">
  <h3 class="abs foot-title" style="left:113px;top:72px">Quick Links</h3>
  <span class="foot-link" style="top:127px">Home</span>
  <span class="foot-link" style="top:165px">Services</span>
  <span class="foot-link" style="top:204px">Contact</span>
  <span class="foot-link" style="top:243px">About</span>
  <span class="foot-link" style="top:281px">Blog</span>

  <h3 class="abs foot-title" style="left:404px;top:72px">Contact Us</h3>
  <svg class="abs" style="left:405px;top:130px" width="16" height="20" viewBox="0 0 16 20" fill="none" stroke="#fff" stroke-width="1.5"><path d="M8 19s6-6.5 6-11A6 6 0 0 0 2 8c0 4.5 6 11 6 11z"/><circle cx="8" cy="8" r="2.2"/></svg>
  <p class="abs foot-text" style="left:444px;top:124px">Suite 210, 48 Harbour Lane<br>Melbourne, VIC , 3000</p>
  <svg class="abs" style="left:405px;top:208px" width="18" height="18" viewBox="0 0 24 24" fill="none" stroke="#fff" stroke-width="1.6"><path d="M5 3h4l2 5-2.5 1.5a11 11 0 0 0 6 6L16 13l5 2v4a2 2 0 0 1-2 2A17 17 0 0 1 3 5a2 2 0 0 1 2-2z"/></svg>
  <p class="abs foot-text" style="left:444px;top:204px">1800 555 019</p>
  <div class="social" style="left:407px;background:#2f6fd0;width:36px;height:36px;top:273px" role="img" aria-label="Social link"></div>
  <div class="social" style="left:460px;width:22px;height:22px;top:280px" role="img" aria-label="Social link"></div>
  <div class="social" style="left:499px;width:22px;height:22px;top:280px;border-radius:50%" role="img" aria-label="Social link"></div>

  <h3 class="abs foot-title" style="left:803px;top:72px">Subscribe for the latest content.</h3>
  <p class="abs foot-text" style="left:803px;top:118px;width:300px">Delivering scalable, cutting-edge solutions with Vestrelle Gold Partner expertise.</p>
  <div class="field" style="left:803px;top:186px;width:284px;height:42px;font-size:13px">Email</div>
  <div class="btn btn-teal" style="left:803px;top:242px;width:137px;height:41px;font-size:14px">Subscribe</div>

  <p class="abs copyright">Copyright © 2025 Corvandel. All rights reserved.</p>
</footer>

</body>
</html>
```